Business Card Design

we are a small based family business that specialise in 12v led lights for velmora caravans.
we also sell 12v switches, wire, circuit breakers, dimmers etc but our main line is LEDs.
We would like something that reflects the LED lighting on our cards.
www.ridgeglowleds.com.au is where you can have a look at to get ideas, of our product.
I have attached the logo we generally use on all our tradix listings and is the main header on our website.

Look forward to seeing what your team comes up with.

Industry/Entity Type

Business

Contact Information for Business Card

Tam 0438 207 915
Quorrin Vale QLD 4399

www.ridgeglowleds.com

```html
<!DOCTYPE html>
<html lang="en">
<head>
<meta charset="utf-8">
<title>Ridgeglow LEDs – Business Card</title>
<link rel="stylesheet" href="https://fonts.googleapis.com/css2?family=Quicksand:wght@400;700&display=swap">
<style>
  :root {
    --brand-red: #b3302a;
    --card-white: #ffffff;
    --page-bg: #e6e6e6;
    --rule-grey: #5f5f5f;
    --rule-light: #9a9a9a;
    --wood-dark: #7a4a22;
    --wood-mid: #b07a45;
    --ceiling: #dcdfe3;
    --curtain: #eeeeee;
    --band-white: rgba(255, 255, 255, 0.55);
  }
  html, body {
    margin: 0;
    padding: 0;
    width: 1200px;
    height: 772px;
    overflow: hidden;
    background: var(--page-bg);
  }
  .business-card {
    position: relative;
    width: 1200px;
    height: 772px;
    background: var(--card-white);
    font-family: "Quicksand", sans-serif;
    overflow: hidden;
  }
  .interior-photo {
    position: absolute;
    left: 0;
    top: 0;
    width: 1200px;
    height: 440px;
    background:
      linear-gradient(180deg,
        var(--wood-dark) 0%,
        var(--wood-mid) 18%,
        var(--ceiling) 22%,
        var(--wood-mid) 34%,
        var(--wood-dark) 52%,
        #3e4a44 58%,
        var(--curtain) 72%,
        #d6d6d6 100%);
  }
  .phone-strip {
    position: absolute;
    left: 0;
    top: 86px;
    width: 529px;
    height: 64px;
    background: var(--card-white);
  }
  .phone-number {
    position: absolute;
    left: 70px;
    top: 84px;
    margin: 0;
    font-size: 56px;
    font-weight: 400;
    line-height: 68px;
    color: var(--brand-red);
    letter-spacing: 1px;
  }
  .details-band {
    position: absolute;
    left: 0;
    top: 326px;
    width: 1200px;
    height: 114px;
    background: var(--band-white);
  }
  .contact-details {
    position: absolute;
    left: 70px;
    top: 338px;
    margin: 0;
    font-size: 31px;
    line-height: 48px;
    color: var(--brand-red);
  }
  .divider-heavy {
    position: absolute;
    left: 0;
    top: 440px;
    width: 1200px;
    height: 10px;
    background: var(--rule-grey);
  }
  .divider-thin {
    position: absolute;
    left: 0;
    top: 458px;
    width: 1200px;
    height: 4px;
    background: var(--rule-light);
  }
  .brand-name {
    position: absolute;
    left: 0;
    top: 548px;
    width: 1200px;
    margin: 0;
    text-align: center;
    font-size: 118px;
    font-weight: 700;
    line-height: 140px;
    color: var(--brand-red);
    letter-spacing: 1px;
  }
</style>
</head>
<body>
  <main class="business-card">
    <div class="interior-photo" role="img" aria-label="Caravan interior with timber overhead cupboards, glowing LED ceiling and cabinet lights, and white curtains"></div>

    <div class="phone-strip"></div>
    <p class="phone-number">0438 207 915</p>

    <div class="details-band"></div>
    <p class="contact-details">
      Quorrin Vale QLD 4399<br>
      www.ridgeglowleds.com
    </p>

    <div class="divider-heavy"></div>
    <div class="divider-thin"></div>

    <h1 class="brand-name">Ridgeglow LEDs</h1>
  </main>
</body>
</html>
```